FinTech company looking to revamp and expand client-facing interface for our financial models

Pellworth Engines currently has a very simple website that allows clients to interact with our financial models. We are looking to completely redesign the current site and add several extra pages to provide extra functionality. We want the design to have a modern, slick feel, that will work on both a desktop or a tablet. It should be straightforward for clients to move between different pages at any time, and clear from the layout how to interact with the more advanced features. We have included screenshots of existing pages in the attached design brief, as well as sketches of the functionality required by the new pages, but can't provide a direct link to the current site.
Target Market(s)
Professional investors that will be paying to access the interface
Industry/Entity Type
Finance
Number of Pages Required
4 page
Colors
Designer to choose colors to be used in the design.
Look and feel
Each slider illustrates characteristics of the customer's brand and the style your logo design should communicate.

```html
<!DOCTYPE html>
<html lang="en">
<head>
<meta charset="utf-8">
<title>Korva · Models · ETF Pairs</title>
<link href="https://fonts.googleapis.com/css2?family=Montserrat:wght@500;600;700&family=Roboto:wght@400;500;700&family=Arimo:wght@400&display=swap" rel="stylesheet">
<style>
  :root{
    --frame:#e6e6e6;
    --page:#f2f2f2;
    --white:#ffffff;
    --navy:#0b3566;
    --teal:#046b6a;
    --ink:#111111;
    --muted:#333333;
    --row-alt:#efefef;
    --rule:#e2e2e2;
    --panel:rgba(34,34,34,0.93);
    --panel-solid:#2e2e2e;
    --tab-black:#141414;
  }
  *{box-sizing:border-box;margin:0;padding:0}
  html,body{width:1200px;height:706px;overflow:hidden;background:var(--frame)}
  .stage{position:absolute;left:0;top:0;width:1300px;height:765px;transform:scale(0.923077);transform-origin:0 0;background:var(--frame);font-family:"Roboto",Arial,sans-serif}
  .app{position:absolute;left:15px;top:15px;width:1270px;height:735px;background:linear-gradient(180deg,#ececec 0%,#f3f3f3 40%,#fafafa 100%);overflow:hidden}

  /* top navigation */
  .topbar{position:absolute;left:0;top:0;width:1270px;height:60px;background:var(--white);box-shadow:0 6px 14px rgba(0,0,0,0.12);display:flex;font-family:"Montserrat",Arial,sans-serif}
  .brand{width:180px;display:flex;align-items:center;padding-left:58px;font-weight:700;font-size:18px;color:var(--ink);letter-spacing:.3px}
  .horizon,.section{display:flex;align-items:center;justify-content:center;font-weight:700;font-size:14px;color:var(--ink);border-right:1px solid var(--rule);gap:8px}
  .horizon{width:90px}
  .horizon.active,.section.active{background:var(--navy);color:var(--white)}
  .spacer{width:135px;border-right:1px solid var(--rule)}
  .section{font-size:13px}
  .section svg{width:22px;height:22px}

  /* tabs */
  .tab{position:absolute;background:var(--white);font-family:"Montserrat",Arial,sans-serif;font-weight:600;font-size:13px;color:#333;display:flex;align-items:center;justify-content:center;border-radius:4px 4px 0 0;box-shadow:0 -1px 4px rgba(0,0,0,0.06)}
  .tab.active{background:var(--tab-black);color:var(--white)}
  .tab-more{position:absolute;left:1175px;top:120px;width:40px;height:35px;background:var(--white);display:flex;align-items:center;justify-content:center}
  .tab-add{position:absolute;left:1220px;top:120px;width:40px;height:35px;background:var(--navy);border-radius:4px 4px 0 0;display:flex;align-items:center;justify-content:center}

  .content{position:absolute;left:0;top:155px;width:1270px;height:580px;background:linear-gradient(180deg,#efefef 0%,#f7f7f7 50%,#fbfbfb 100%)}
  .export{position:absolute;left:1150px;top:197px;display:flex;align-items:center;gap:8px;font-family:"Montserrat",Arial,sans-serif;font-weight:700;font-size:17px;color:var(--navy)}

  /* table */
  .models{position:absolute;left:90px;top:235px;width:1160px;border-radius:6px;overflow:hidden;box-shadow:0 3px 8px rgba(0,0,0,0.10);background:var(--white)}
  .row{display:grid;grid-template-columns:100px 140px 115px 85px repeat(8,90px);height:70px}
  .row > div{display:flex;align-items:center;padding-left:9px;font-family:"Arimo",Arial,sans-serif;font-size:16px;color:var(--ink);border-right:1px solid var(--rule);line-height:1.3}
  .row.head{background:var(--teal)}
  .row.head > div{font-family:"Montserrat",Arial,sans-serif;font-weight:600;font-size:17px;color:var(--white);justify-content:center;padding-left:0;border-right:1px solid rgba(255,255,255,0.15)}
  .row.alt{background:var(--row-alt)}

  /* filter drawer */
  .filters{position:absolute;left:0;top:155px;width:445px;height:580px;background:var(--panel);color:var(--white)}
  .filters h2{position:absolute;left:184px;top:84px;font-family:"Montserrat",Arial,sans-serif;font-weight:700;font-size:19px}
  .field{position:absolute;left:40px;display:flex;align-items:center;font-size:17px;font-weight:500}
  .field .label{width:86px}
  .field .sub{margin-left:0;width:100px}
  .field input{width:180px;height:31px;border:none;border-radius:4px;padding-left:12px;font-family:"Roboto",Arial,sans-serif;font-size:17px;color:var(--ink);background:var(--white)}
  .apply{position:absolute;left:40px;top:280px;display:flex;align-items:center;font-size:17px;font-weight:500;gap:0}
  .check{width:19px;height:19px;background:var(--white);border-radius:3px;display:inline-block;margin:0 8px 0 0}
  .search{position:absolute;left:145px;top:340px;width:155px;height:50px;background:var(--navy);border:2px solid var(--white);border-radius:6px;color:var(--white);font-family:"Roboto",Arial,sans-serif;font-weight:500;font-size:16px;display:flex;align-items:center;justify-content:center}
  .close-tab{position:absolute;left:445px;top:320px;width:50px;height:250px;background:var(--panel-solid);border-radius:0 5px 5px 0;display:flex;align-items:center;justify-content:center}
  .close-tab span{transform:rotate(-90deg);white-space:nowrap;font-family:"Montserrat",Arial,sans-serif;font-weight:600;font-size:15px;letter-spacing:.6px;color:var(--white)}
  .close-knob{position:absolute;left:482px;top:432px;width:26px;height:26px}
</style>
</head>
<body>
<div class="stage">
  <div class="app">
    <nav class="topbar">
      <div class="brand">KORVA</div>
      <div class="horizon active">250D</div>
      <div class="horizon">83D</div>
      <div class="horizon">42D</div>
      <div class="spacer"></div>
      <div class="section active" style="width:142px">
        <svg viewBox="0 0 24 24" fill="none" stroke="#fff" stroke-width="2"><path d="M3 11 12 3l9 8"/><path d="M5 10v10h5v-6h4v6h5V10"/></svg>MODELS</div>
      <div class="section" style="width:176px">
        <svg viewBox="0 0 24 24" fill="#222"><circle cx="12" cy="12" r="3.5"/><circle cx="12" cy="3" r="1.6"/><circle cx="12" cy="21" r="1.6"/><circle cx="3" cy="12" r="1.6"/><circle cx="21" cy="12" r="1.6"/><circle cx="5.6" cy="5.6" r="1.6"/><circle cx="18.4" cy="18.4" r="1.6"/><circle cx="5.6" cy="18.4" r="1.6"/><circle cx="18.4" cy="5.6" r="1.6"/></svg>SENSITIVITIES</div>
      <div class="section" style="width:160px">
        <svg viewBox="0 0 24 24" fill="none" stroke="#222" stroke-width="2"><circle cx="7" cy="7" r="4"/><circle cx="17" cy="7" r="4"/><circle cx="7" cy="17" r="4"/><circle cx="17" cy="17" r="4"/></svg>PORTFOLIO</div>
      <div class="section" style="width:152px">
        <svg viewBox="0 0 24 24" fill="none" stroke="#222" stroke-width="2"><rect x="2" y="3" width="20" height="18" rx="1"/><path d="M5 16l4-5 4 3 6-7"/></svg>BACKTEST</div>
    </nav>

    <div class="tab" style="left:55px;top:120px;width:155px;height:35px">EQUITIES</div>
    <div class="tab" style="left:215px;top:120px;width:155px;height:35px">ETFS</div>
    <div class="tab" style="left:375px;top:110px;width:155px;height:45px">PAIRS</div>
    <div class="tab active" style="left:535px;top:100px;width:155px;height:55px">ETF PAIRS</div>
    <div class="tab" style="left:695px;top:110px;width:155px;height:45px">FACTORS</div>
    <div class="tab" style="left:855px;top:120px;width:155px;height:35px">NEW TAB TITLE #1</div>
    <div class="tab" style="left:1015px;top:120px;width:155px;height:35px">NEW TAB TITLE #2</div>
    <div class="tab-more"><svg width="14" height="20" viewBox="0 0 14 20"><path d="M3 2l8 8-8 8" fill="none" stroke="#999" stroke-width="3"/></svg></div>
    <div class="tab-add"><svg width="26" height="26" viewBox="0 0 26 26" fill="none" stroke="#fff" stroke-width="2"><circle cx="13" cy="13" r="11"/><path d="M13 7v12M7 13h12"/></svg></div>

    <div class="content"></div>

    <div class="export">
      <svg width="26" height="24" viewBox="0 0 26 24" fill="none" stroke="#0b3566" stroke-width="2.4"><path d="M11 5H3v17h17v-8"/><path d="M9 15c1-6 6-9 13-9"/><path d="M17 2l5 4-4 5"/></svg>Export
    </div>

    <div class="models">
      <div class="row head"><div>ID ⌄</div><div>Sector</div><div>Time</div><div>Quality</div><div>Stat 1</div><div>Stat 2</div><div>Stat 3</div><div>Stat 4</div><div>Stat 5</div><div>Stat 6</div><div>Stat 7</div><div>Stat 8</div></div>
      <div class="row"><div>Model 1</div><div>Materials</div><div>2019-07-03<br>12:15:00.000</div><div>30.2288</div><div>2.01574</div><div>23.305</div><div>-0.149368</div><div>22.3054</div><div>4.63714</div><div>0.945706</div><div>2.81949</div><div>2.60858</div></div>
      <div class="row alt"><div>Model 2</div><div>Industrials</div><div>2019-07-03<br>12:15:00.000</div><div>18.8694</div><div>0.87307</div><div>32.185</div><div>-0.033692</div><div>33.9911</div><div>11.5693</div><div>-0.472968</div><div>-0.830458</div><div>6.80646</div></div>
      <div class="row"><div>Model 3</div><div>Consumer Discretionary</div><div>2019-07-03<br>12:15:00.000</div><div>56.6002</div><div>-0.569222</div><div>159.814</div><div>0.0252328</div><div>172.616</div><div>10.2875</div><div>-0.750396</div><div>-0.385309</div><div>4.69146</div></div>
      <div class="row alt"><div>Model 4</div><div>Information Technology</div><div>2019-07-03<br>12:15:00.000</div><div>45.6856</div><div>0.412148</div><div>202.488</div><div>0.0084923</div><div>205.834</div><div>11.9094</div><div>-0.137913</div><div>0.449595</div><div>3.85106</div></div>
      <div class="row"><div>Model 5</div><div>Information Technology</div><div>2019-07-03<br>12:15:00.000</div><div>75.7733</div><div>7.06728</div><div>188.605</div><div>0.016913</div><div>161.665</div><div>3.82241</div><div>0.981019</div><div>1.29847</div><div>3.34927</div></div>
    </div>

    <aside class="filters">
      <h2>FILTERS</h2>
      <div class="field" style="top:155px"><span class="label">Quality</span><span class="sub">Threshold:</span><input type="text" value="-10"></div>
      <div class="field" style="top:215px"><span class="label">Abs. Stat</span><span class="sub">Threshold:</span><input type="text" value="-10"></div>
      <div class="apply"><span style="margin-right:16px">Apply Filter</span><span class="check"></span><span style="margin-right:16px">All tabs</span><span class="check"></span><span>Current tab</span></div>
      <div class="search">SEARCH</div>
    </aside>
    <div class="close-tab"><span>CLOSE FILTERS</span></div>
    <svg class="close-knob" viewBox="0 0 26 26"><circle cx="13" cy="13" r="12" fill="#0b3566" stroke="#fff" stroke-width="1.5"/><path d="M19 13H8M12 8.5 7.5 13l4.5 4.5" fill="none" stroke="#fff" stroke-width="2"/></svg>
  </div>
</div>
</body>
</html>
```